Thornfield Apex Stickers - Crossfit Box

We want a variety of stickers, something between 3 to 6 stickers that will be mostly added to Cars, Coolers, Shakers, and we want them to identify our brand.

Attached we will provide some of our logos, names, concepts, with the hopes you will be able to identify the brand and provide us with a few stickers such as

Thornfield Apex box
designs with the viking and perhaps a "female Viking"
The Name of the box minimized such as "TFX" with some art.

Anyways, few ideas that could end up in stickers. Horizontal, Vertical, Rounded and Die cut Stickers

```html
<!DOCTYPE html>
<html lang="en">
<head>
<meta charset="utf-8">
<title>Thornfield Apex – Armor Up Sticker</title>
<link rel="stylesheet" href="https://fonts.googleapis.com/css2?family=Alfa+Slab+One&display=swap">
<style>
  :root {
    --gold: #ba9a60;
    --ink: #0d0d0d;
    --paper: #ffffff;
    --emblem-dark: #1c1a17;
    --emblem-mid: #6e5c3c;
  }
  html, body {
    margin: 0;
    padding: 0;
    width: 1200px;
    height: 644px;
    overflow: hidden;
    background: var(--gold);
  }
  .sticker {
    display: block;
    width: 1200px;
    height: 644px;
    background: var(--gold);
  }
  .slab {
    font-family: "Alfa Slab One", serif;
  }
  .ink { fill: var(--ink); }
  .paper { fill: var(--paper); }
  .divider { stroke: var(--ink); stroke-width: 4; }
</style>
</head>
<body>
<svg class="sticker" viewBox="0 0 1200 644" width="1200" height="644" xmlns="http://www.w3.org/2000/svg">
  <defs>
    <linearGradient id="emblemTone" x1="0" y1="0" x2="1" y2="1">
      <stop offset="0" stop-color="var(--emblem-mid)"/>
      <stop offset="1" stop-color="var(--emblem-dark)"/>
    </linearGradient>
  </defs>

  <!-- Left call to action -->
  <g class="join-block slab ink">
    <text class="join-word" x="183" y="358" font-size="148" textLength="355" lengthAdjust="spacingAndGlyphs">JOIN</text>
    <line class="divider" x1="49" y1="376" x2="421" y2="376"/>
    <text class="the-word" x="451" y="405" font-size="44" textLength="79" lengthAdjust="spacingAndGlyphs">THE</text>
    <text class="name-word" x="49" y="491" font-size="91" textLength="489" lengthAdjust="spacingAndGlyphs">THORNFIELD</text>
  </g>

  <!-- Centre emblem area -->
  <rect class="emblem" x="550" y="110" width="268" height="410" rx="20"
        fill="url(#emblemTone)" role="img"
        aria-label="Illustration of a bearded viking warrior in a horned helmet on a shield with two crossed spears"/>

  <!-- Right call to action -->
  <g class="armor-block slab">
    <text class="armor-word paper" x="836" y="289" font-size="60" textLength="246" lengthAdjust="spacingAndGlyphs">ARMOR</text>
    <text class="up-word paper" x="844" y="447" font-size="182" textLength="238" lengthAdjust="spacingAndGlyphs">UP</text>
    <text class="brand-name ink" x="844" y="507" font-size="58" textLength="128" lengthAdjust="spacingAndGlyphs">TFX</text>
    <text class="brand-sub ink" x="844" y="520" font-size="7" textLength="128" lengthAdjust="spacing">APEX BOX</text>
  </g>
</svg>
</body>
</html>
```